Professional & attention grabbing.

A business card design, front and back. I already have a logo I will attach, but I am open to something new as well.
Things to include:
Name:
Title:
Phone:
Email:
Wanting something that is professional but attention grabbing.
Also we do a lot of work using drones on natural gas pipelines (leading the future)if you want to include any of that. I'm open to ideas.
Target Market(s)
Natural gas transmission industry / greenhouse gas mitigation industry
Industry/Entity Type
Business
Colors
Designer to choose colors to be used in the design.
Look and feel
Each slider illustrates characteristics of the customer's brand and the style your logo design should communicate.

```html
<!DOCTYPE html>
<html lang="en">
<head>
<meta charset="utf-8">
<title>Kestrel Line Inspections – Business Card</title>
<link href="https://fonts.googleapis.com/css2?family=Roboto+Condensed:wght@300;400;700&display=swap" rel="stylesheet">
<style>
  :root {
    --brand-red: #c4161c;
    --brand-red-dark: #9e1015;
    --charcoal: #3a3a3c;
    --ink: #4a4a4c;
    --paper: #ffffff;
    --backdrop: #e4e4e6;
  }
  * { box-sizing: border-box; margin: 0; padding: 0; }
  html, body { width: 1200px; height: 950px; overflow: hidden; }
  body {
    background: var(--backdrop);
    font-family: "Roboto Condensed", Arial, sans-serif;
    display: flex;
    flex-direction: column;
    align-items: center;
    justify-content: center;
    gap: 50px;
  }
  .card {
    position: relative;
    width: 700px;
    height: 400px;
    overflow: hidden;
    box-shadow: 0 10px 30px rgba(0,0,0,.18);
  }
  .card__shapes { position: absolute; inset: 0; }

  /* front */
  .card--front { background: var(--paper); }
  .brand {
    position: absolute;
    display: flex;
    align-items: center;
    gap: 14px;
  }
  .brand__mark { width: 26px; height: 26px; background: var(--brand-red); flex: none; }
  .brand__name {
    font-weight: 700;
    text-transform: uppercase;
    letter-spacing: .5px;
    line-height: 1;
  }
  .card--front .brand { top: 92px; right: 200px; }
  .card--front .brand__name { color: var(--charcoal); font-size: 30px; }

  .contact { position: absolute; left: 190px; bottom: 52px; }
  .contact__name {
    color: var(--brand-red);
    font-size: 24px;
    font-weight: 400;
    text-transform: uppercase;
    letter-spacing: .5px;
  }
  .contact__title {
    color: var(--ink);
    font-size: 18px;
    font-weight: 300;
    text-transform: uppercase;
    margin-bottom: 16px;
  }
  .contact__list { list-style: none; }
  .contact__item {
    display: flex;
    align-items: center;
    gap: 12px;
    color: var(--ink);
    font-size: 17px;
    font-weight: 300;
    line-height: 28px;
  }
  .contact__icon { width: 16px; height: 16px; flex: none; }

  /* back */
  .card--back {
    background: linear-gradient(135deg, var(--brand-red) 0%, var(--brand-red-dark) 100%);
  }
  .card--back .brand {
    top: 50%; left: 50%;
    transform: translate(-50%, -50%);
  }
  .card--back .brand__mark { background: var(--paper); }
  .card--back .brand__name { color: var(--paper); font-size: 38px; }
  .web-address {
    position: absolute;
    left: 0; right: 0; bottom: 36px;
    text-align: center;
    color: var(--paper);
    font-size: 15px;
    font-weight: 300;
    letter-spacing: 8px;
  }
</style>
</head>
<body>

  <section class="card card--front" aria-label="Card front">
    <svg class="card__shapes" viewBox="0 0 700 400" preserveAspectRatio="none" aria-hidden="true">
      <path d="M0 0 H95 C120 70 60 120 60 190 C60 270 140 300 140 400 H0 Z" fill="var(--brand-red)"/>
      <path d="M520 0 H700 V150 C660 150 640 110 620 70 C600 30 570 5 520 0 Z" fill="var(--charcoal)"/>
    </svg>

    <div class="brand">
      <span class="brand__mark"></span>
      <span class="brand__name">Kestrel Line Inspections</span>
    </div>

    <div class="contact">
      <p class="contact__name">Mara Ellison</p>
      <p class="contact__title">President</p>
      <ul class="contact__list">
        <li class="contact__item">
          <svg class="contact__icon" viewBox="0 0 16 16" aria-hidden="true">
            <circle cx="8" cy="8" r="8" fill="var(--brand-red)"/>
            <path d="M5.2 4.2l1.4 1.6-.8 1c.5 1.1 1.3 1.9 2.4 2.4l1-.8 1.6 1.4-.8 1.5C7 11 5 9 4.5 5l.7-.8z" fill="#fff"/>
          </svg>
          555 0142 7781
        </li>
        <li class="contact__item">
          <svg class="contact__icon" viewBox="0 0 16 16" aria-hidden="true">
            <circle cx="8" cy="8" r="8" fill="var(--brand-red)"/>
            <rect x="4" y="5.2" width="8" height="5.6" fill="#fff"/>
            <path d="M4 5.2l4 3 4-3" fill="none" stroke="var(--brand-red)" stroke-width="1"/>
          </svg>
          mara@kestrelline.com
        </li>
        <li class="contact__item">
          <svg class="contact__icon" viewBox="0 0 16 16" aria-hidden="true">
            <circle cx="8" cy="8" r="8" fill="var(--brand-red)"/>
            <circle cx="8" cy="8" r="4" fill="none" stroke="#fff" stroke-width="1"/>
            <path d="M4 8h8M8 4c-2 2.5-2 5.5 0 8M8 4c2 2.5 2 5.5 0 8" fill="none" stroke="#fff" stroke-width=".8"/>
          </svg>
          www.kestrelline.com
        </li>
      </ul>
    </div>
  </section>

  <section class="card card--back" aria-label="Card back">
    <div class="brand">
      <span class="brand__mark"></span>
      <span class="brand__name">Kestrel Line Inspections</span>
    </div>
    <p class="web-address">www.kestrelline.com</p>
  </section>

</body>
</html>
```